Premium Organic Ceremonial Matcha Green Tea - Product Label

Two Label Bag Sizes: 18x30cm and 17x24cm

Be EXTRA Creative.. please message me with any questions and I will respond quickly.

Target Market(s)

Health, Organic, Green Tea Matcha Drinkers

Industry/Entity Type

Product

Requirements
Must have
• Organic Matcha Green Tea
• Try to incorporate geometry in logo into design... not mandatory but preferred for branding.

```html
<!DOCTYPE html>
<html lang="en">
<head>
<meta charset="utf-8">
<title>Verdant Grove Organic Matcha – Pouch Label</title>
<link href="https://fonts.googleapis.com/css2?family=Varela+Round&display=swap" rel="stylesheet">
<style>
  :root {
    --bg: #e9efe6;
    --label: #ffffff;
    --green: #2f8a2c;
    --green-light: #5cab3d;
    --matcha: #8fbf3a;
    --matcha-pale: #c9e08a;
    --yellow: #e3b51c;
    --text: #3a3a3a;
    --hill-dark: #1f5a22;
    --hill-light: #4f9a35;
    --sky: #2f6b5a;
    --cup: #1c201c;
  }
  * { box-sizing: border-box; margin: 0; padding: 0; }
  html, body { width: 1200px; height: 921px; overflow: hidden; }
  body {
    background: var(--bg);
    font-family: "Varela Round", sans-serif;
    color: var(--text);
    position: relative;
  }
  .pouch-label {
    position: absolute;
    left: 340px; top: 50px;
    width: 520px; height: 820px;
    background: var(--label);
    border-radius: 6px;
    overflow: hidden;
    box-shadow: 0 6px 24px rgba(0,0,0,.15);
  }
  .landscape-band {
    position: absolute; left: 0; top: 0; width: 520px; height: 260px;
  }
  .hang-slot {
    position: absolute; left: 215px; top: 46px;
    width: 110px; height: 26px; border-radius: 13px;
    background: var(--bg);
  }
  .brand-box {
    position: absolute; left: 0; top: 170px;
    width: 290px; height: 150px;
    background: var(--label);
    border: 3px solid var(--green);
    border-left: none;
    box-shadow: 0 2px 8px rgba(0,0,0,.2);
  }
  .brand-tree {
    position: absolute; left: 70px; top: 16px; width: 140px; height: 76px;
    border-radius: 10px;
    background: linear-gradient(135deg, var(--green-light), var(--matcha-pale));
    opacity: .8;
  }
  .brand-name {
    position: absolute; left: 0; right: 0; top: 102px;
    text-align: center;
    font-size: 26px; color: var(--green);
  }
  .organic-seal {
    position: absolute; left: 418px; top: 210px;
    width: 78px; height: 78px; border-radius: 50%;
    background: var(--label);
    border: 6px solid var(--green);
  }
  .powder-spoon {
    position: absolute; left: 335px; top: 290px; width: 110px; height: 56px;
    border-radius: 28px;
    background: linear-gradient(135deg, #d9c49a, var(--matcha) 60%);
  }
  .headline {
    position: absolute; left: 40px; top: 352px;
    font-size: 21px; color: var(--green);
  }
  .headline span { color: var(--yellow); }
  .benefits {
    position: absolute; left: 40px; top: 395px;
    list-style: none;
  }
  .benefits li {
    display: flex; align-items: center; gap: 10px;
    height: 35px; font-size: 15px;
  }
  .benefits svg { width: 22px; height: 22px; flex: none; }
  .uses {
    position: absolute; left: 282px; top: 400px;
    display: flex; gap: 14px;
  }
  .use { width: 60px; text-align: center; font-size: 11px; color: var(--green); }
  .use-ring {
    width: 58px; height: 58px; border-radius: 50%;
    border: 2px solid var(--green-light);
    display: flex; align-items: center; justify-content: center;
    margin-bottom: 5px;
  }
  .use-ring svg { width: 30px; height: 30px; }
  .latte-photo {
    position: absolute; left: 250px; top: 540px; width: 250px; height: 250px;
    border-radius: 24px;
    background: radial-gradient(circle at 40% 30%, var(--matcha-pale) 0%, var(--matcha) 28%, #3f5a2a 55%, var(--cup) 80%);
  }
  .net-weight {
    position: absolute; left: 40px; top: 710px;
    font-size: 11px; color: var(--text);
  }
  .net-weight strong { display: block; font-weight: normal; font-size: 15px; margin-top: 6px; }
</style>
</head>
<body>
  <section class="pouch-label">
    <svg class="landscape-band" role="img" aria-label="Photo of green terraced tea hills under a misty sky" viewBox="0 0 520 260" preserveAspectRatio="none">
      <defs>
        <linearGradient id="hills" x1="0" y1="0" x2="0" y2="1">
          <stop offset="0" stop-color="var(--sky)"/>
          <stop offset=".45" stop-color="var(--hill-light)"/>
          <stop offset="1" stop-color="var(--hill-dark)"/>
        </linearGradient>
      </defs>
      <path d="M0 0H520V200Q440 215 400 260H0Z" fill="url(#hills)"/>
    </svg>
    <div class="hang-slot"></div>

    <div class="brand-box">
      <div class="brand-tree" role="img" aria-label="Illustration of a tree beside a honeycomb pattern"></div>
      <div class="brand-name">Verdant Grove</div>
    </div>

    <div class="organic-seal" aria-hidden="true"></div>

    <div class="powder-spoon" role="img" aria-label="Photo of matcha powder on a wooden spoon"></div>

    <h1 class="headline">100% Pure <span>Organic Matcha</span></h1>

    <ul class="benefits">
      <li><svg viewBox="0 0 22 22"><rect x="2" y="4" width="15" height="15" rx="3" fill="none" stroke="var(--green)" stroke-width="2"/><path d="M6 11l4 4 9-11" fill="none" stroke="var(--green)" stroke-width="2.5" stroke-linecap="round"/></svg>Antioxidants Powerhouse</li>
      <li><svg viewBox="0 0 22 22"><rect x="2" y="4" width="15" height="15" rx="3" fill="none" stroke="var(--green)" stroke-width="2"/><path d="M6 11l4 4 9-11" fill="none" stroke="var(--green)" stroke-width="2.5" stroke-linecap="round"/></svg>Fat Burner</li>
      <li><svg viewBox="0 0 22 22"><rect x="2" y="4" width="15" height="15" rx="3" fill="none" stroke="var(--green)" stroke-width="2"/><path d="M6 11l4 4 9-11" fill="none" stroke="var(--green)" stroke-width="2.5" stroke-linecap="round"/></svg>Increases Mental Focus</li>
      <li><svg viewBox="0 0 22 22"><rect x="2" y="4" width="15" height="15" rx="3" fill="none" stroke="var(--green)" stroke-width="2"/><path d="M6 11l4 4 9-11" fill="none" stroke="var(--green)" stroke-width="2.5" stroke-linecap="round"/></svg>Energy Booster</li>
      <li><svg viewBox="0 0 22 22"><rect x="2" y="4" width="15" height="15" rx="3" fill="none" stroke="var(--green)" stroke-width="2"/><path d="M6 11l4 4 9-11" fill="none" stroke="var(--green)" stroke-width="2.5" stroke-linecap="round"/></svg>Culinary Grade</li>
      <li><svg viewBox="0 0 22 22"><rect x="2" y="4" width="15" height="15" rx="3" fill="none" stroke="var(--green)" stroke-width="2"/><path d="M6 11l4 4 9-11" fill="none" stroke="var(--green)" stroke-width="2.5" stroke-linecap="round"/></svg>Maximum Potency</li>
    </ul>

    <div class="uses">
      <div class="use">
        <div class="use-ring"><svg viewBox="0 0 30 30"><path d="M9 8h12l-2 19h-8z" fill="none" stroke="var(--green)" stroke-width="2"/><path d="M13 3v3M17 3v3" stroke="var(--green)" stroke-width="1.5"/></svg></div>
        Smoothies
      </div>
      <div class="use">
        <div class="use-ring"><svg viewBox="0 0 30 30"><path d="M7 15h16l-3 11H10z" fill="none" stroke="var(--green)" stroke-width="2"/><path d="M7 15q0-9 8-9t8 9" fill="none" stroke="var(--green)" stroke-width="2"/></svg></div>
        Baking
      </div>
      <div class="use">
        <div class="use-ring"><svg viewBox="0 0 30 30"><path d="M6 11h15v8a5 5 0 0 1-5 5h-5a5 5 0 0 1-5-5z" fill="none" stroke="var(--green)" stroke-width="2"/><path d="M21 13h2a3 3 0 0 1 0 6h-2M4 27h19" fill="none" stroke="var(--green)" stroke-width="2"/></svg></div>
        Lattes
      </div>
    </div>

    <div class="latte-photo" role="img" aria-label="Photo of two black cups of matcha latte with foam art"></div>

    <p class="net-weight">Net weight<strong>113g / 4oz</strong></p>
  </section>
</body>
</html>
```